Corvane Capital Business Cards

These are professional business cards that are for my family office.
Put fake emails and phone numbers as of now until I finalize those components. This family office controls my families investments, assets, and future. The cards should be professional.
..
.
.
.
I just uploaded another variation of a logo I would like to see as a business card to I am inbeteen which logo to use

Target Market(s)

business

Industry/Entity Type

business

Contact Information for Business Card

Professional, wealth related, finance related.

Requirements
Must have
• Logo

```html
<!DOCTYPE html>
<html lang="en">
<head>
<meta charset="utf-8">
<title>Corvane Capital – Business Cards</title>
<link href="https://fonts.googleapis.com/css2?family=Cinzel:wght@500&family=Montserrat:wght@400;500;600&display=swap" rel="stylesheet">
<style>
  :root {
    --backdrop: #a9a9a9;
    --navy: #1a1f2e;
    --navy-deep: #161a27;
    --paper: #ebebeb;
    --paper-light: #f1f1f1;
    --ink: #111111;
    --ink-soft: #555555;
    --white: #ffffff;
  }
  * { margin: 0; padding: 0; box-sizing: border-box; }
  html, body {
    width: 1200px;
    height: 1000px;
    overflow: hidden;
    background: var(--backdrop);
  }
  .stage {
    position: relative;
    width: 1200px;
    height: 1000px;
  }
  .card {
    position: absolute;
    left: 234px;
    width: 733px;
    height: 422px;
    overflow: hidden;
  }
  .card--front { top: 57px; background: var(--navy); }
  .card--back  { top: 503px; background: var(--paper); }

  .front-pattern {
    position: absolute;
    inset: 0;
    background: linear-gradient(90deg, var(--navy) 0%, var(--navy-deep) 100%);
  }
  .front-wordmark {
    position: absolute;
    left: 0;
    right: 0;
    top: 190px;
    text-align: center;
    font-family: "Cinzel", serif;
    font-weight: 500;
    font-size: 50px;
    line-height: 1;
    color: var(--white);
    letter-spacing: 1px;
  }

  .back-emboss {
    position: absolute;
    left: 350px;
    top: 66px;
    width: 383px;
    height: 356px;
    background: radial-gradient(circle at 60% 60%, var(--paper-light) 0%, var(--paper) 70%);
  }
  .back-wordmark {
    position: absolute;
    left: 58px;
    top: 133px;
    font-family: "Cinzel", serif;
    font-weight: 500;
    font-size: 22px;
    line-height: 1;
    color: var(--ink);
  }
  .holder-name {
    position: absolute;
    left: 57px;
    top: 228px;
    font-family: "Montserrat", sans-serif;
    font-weight: 600;
    font-size: 25px;
    color: var(--ink);
  }
  .holder-position {
    position: absolute;
    left: 58px;
    top: 261px;
    font-family: "Montserrat", sans-serif;
    font-weight: 500;
    font-size: 10px;
    letter-spacing: 2px;
    color: var(--ink);
  }
  .contact-list {
    position: absolute;
    left: 58px;
    top: 304px;
    list-style: none;
    font-family: "Montserrat", sans-serif;
    font-weight: 400;
    font-size: 20px;
    line-height: 24.5px;
    color: var(--ink-soft);
  }
  .contact-list b { font-weight: 600; }
</style>
</head>
<body>
  <main class="stage">
    <section class="card card--front">
      <div class="front-pattern" role="img" aria-label="Tonal repeating monogram pattern on navy"></div>
      <div class="front-wordmark">CORVANE CAPITAL</div>
    </section>

    <section class="card card--back">
      <div class="back-emboss" role="img" aria-label="Blind-embossed monogram decoration"></div>
      <div class="back-wordmark">CORVANE CAPITAL</div>
      <div class="holder-name">Name Surname</div>
      <div class="holder-position">POSITION</div>
      <ul class="contact-list">
        <li><b>o:</b> 123 456 7890</li>
        <li><b>e:</b> email@website.com</li>
        <li><b>w:</b> website.com</li>
      </ul>
    </section>
  </main>
</body>
</html>
```